Clear Plastic Card Design

I am looking to have a business card designed from my logo icon. I am looking to match the style of a different business card I have attached in the files.
Looking for a card that is plastic, with layers of transparency in the shape of my logo icon (also attached in the files) - not a circle like the other card. The winning design will incorporate the red icon logo on the front and back and include the charity's name, "Light for the Weary Souls" in the same or similar font, as well as an email and phone number. For now, use the email: email@lightfortheweary-mail.org and the phone number 555-382-7194.
We like how the sample business card has transparency, partial and full opacity layers and a matching color scheme. Files will need to be in vector so that our business card printing company can work with it.
UPDATE:
We've some excellent designs in, thank you everyone! I got an early review from the owner, and he requested a minor redirect to find his perfect design. He wants the design to stand out by NOT being a rectangle. Try instead a circle, square, or best yet - something that falls in the outline of the logo icon, either fully or partially. Thank you, everyone!
Light for the Weary Souls text should be incorporated as well as a phone and email.

```html
<!DOCTYPE html>
<html lang="en">
<head>
<meta charset="utf-8">
<title>Light for the Weary Souls — Business Cards</title>
<link rel="stylesheet" href="https://fonts.googleapis.com/css2?family=Questrial&family=Arimo:wght@400;700&display=swap">
<style>
  :root {
    --page: #e8e5e1;
    --card: #ffffff;
    --sand: #ebe6e0;
    --sand-light: #f4f1ed;
    --ring: rgba(255,255,255,0.85);
    --accent: #dc4a26;
    --ink: #111111;
  }
  html, body {
    margin: 0;
    padding: 0;
    width: 1195px;
    height: 1200px;
    overflow: hidden;
    background: var(--page);
  }
  .canvas {
    position: relative;
    width: 1195px;
    height: 1200px;
  }
  .card {
    position: absolute;
    left: 226px;
    width: 743px;
    height: 423px;
    filter: drop-shadow(0 6px 14px rgba(0,0,0,0.12));
  }
  .card--front { top: 140px; }
  .card--back  { top: 664px; }
  .card svg { display: block; width: 100%; height: 100%; overflow: visible; }
  .title { font-family: "Questrial", sans-serif; fill: var(--ink); }
  .brand-name { font-family: "Questrial", sans-serif; fill: var(--accent); }
  .contact { font-family: "Arimo", sans-serif; fill: var(--ink); }
  .contact--bold { font-weight: 700; }
</style>
</head>
<body>
<main class="canvas">

  <!-- Front: straight left edge, right end follows the round logo disc -->
  <div class="card card--front">
    <svg viewBox="0 0 895 510" xmlns="http://www.w3.org/2000/svg">
      <defs>
        <clipPath id="front-shape">
          <path d="M50,0 H640 A255,255 0 0 1 640,510 H50 Q0,510 0,460 V50 Q0,0 50,0 Z"/>
        </clipPath>
      </defs>
      <g clip-path="url(#front-shape)">
        <rect class="card-base" width="895" height="510" fill="var(--card)"/>
        <path class="sand-wave" d="M0,0 H895 V400 C820,430 720,470 580,420 C470,370 380,300 230,300 C140,300 60,250 0,195 Z" fill="var(--sand)"/>
        <g class="rings" fill="none" stroke="var(--ring)" stroke-width="2">
          <circle cx="660" cy="255" r="185"/>
          <circle cx="660" cy="255" r="230" stroke-dasharray="30 40"/>
          <circle cx="660" cy="255" r="290"/>
          <circle cx="660" cy="255" r="360" stroke-dasharray="20 60"/>
        </g>
        <rect class="hands-illustration" role="img" aria-label="Illustration of raised hands reaching up toward floating hearts" x="60" y="30" width="230" height="270" rx="20" fill="var(--sand-light)"/>
        <circle class="logo-disc" cx="660" cy="255" r="152" fill="var(--card)"/>
        <text class="brand-name" x="660" y="246" font-size="28" text-anchor="middle">Light for the</text>
        <text class="brand-name" x="660" y="280" font-size="28" text-anchor="middle">Weary Souls</text>
        <rect class="edge-bar" x="0" y="105" width="10" height="298" fill="var(--accent)"/>
        <path class="edge-arc" d="M844.8,111.6 A250,250 0 0 1 844.8,398.4" fill="none" stroke="var(--accent)" stroke-width="10"/>
      </g>
      <text class="title" x="32" y="382" font-size="62">Light for the</text>
      <text class="title" x="32" y="440" font-size="56">Weary Souls</text>
      <text class="contact contact--bold" x="40" y="474" font-size="20">www.lightfortheweary-souls.org</text>
    </svg>
  </div>

  <!-- Back: left end follows the round logo disc, straight right edge -->
  <div class="card card--back">
    <svg viewBox="0 0 895 510" xmlns="http://www.w3.org/2000/svg">
      <defs>
        <clipPath id="back-shape">
          <path d="M255,0 H845 Q895,0 895,50 V460 Q895,510 845,510 H255 A255,255 0 0 1 255,0 Z"/>
        </clipPath>
      </defs>
      <g clip-path="url(#back-shape)">
        <rect class="card-base" width="895" height="510" fill="var(--card)"/>
        <path class="sand-wave" d="M0,0 H895 V180 C860,250 800,300 680,310 C560,320 480,340 400,390 C300,450 150,440 0,400 Z" fill="var(--sand)"/>
        <g class="rings" fill="none" stroke="var(--ring)" stroke-width="2">
          <circle cx="240" cy="255" r="185"/>
          <circle cx="240" cy="255" r="230" stroke-dasharray="30 40"/>
          <circle cx="240" cy="255" r="290"/>
          <circle cx="240" cy="255" r="360" stroke-dasharray="20 60"/>
        </g>
        <rect class="hands-illustration" role="img" aria-label="Illustration of raised hands reaching up toward floating hearts" x="605" y="30" width="230" height="270" rx="20" fill="var(--sand-light)"/>
        <circle class="logo-disc" cx="240" cy="255" r="152" fill="var(--card)"/>
        <text class="brand-name" x="240" y="246" font-size="28" text-anchor="middle">Light for the</text>
        <text class="brand-name" x="240" y="280" font-size="28" text-anchor="middle">Weary Souls</text>
        <path class="edge-arc" d="M50.2,111.6 A250,250 0 0 0 50.2,398.4" fill="none" stroke="var(--accent)" stroke-width="10"/>
        <rect class="edge-bar" x="885" y="105" width="10" height="298" fill="var(--accent)"/>
      </g>
      <text class="title" x="856" y="360" font-size="46" text-anchor="end">Light for the</text>
      <text class="title" x="856" y="408" font-size="46" text-anchor="end">Weary Souls</text>
      <text class="contact" x="812" y="452" font-size="20" text-anchor="end">555-382-7194</text>
      <g class="icon icon--phone" fill="none" stroke="var(--ink)" stroke-width="2">
        <circle cx="841" cy="445" r="13"/>
        <rect x="836" y="437" width="10" height="16" rx="2"/>
      </g>
      <text class="contact" x="812" y="486" font-size="20" text-anchor="end">email@lightfortheweary-mail.org</text>
      <g class="icon icon--mail">
        <circle cx="841" cy="479" r="13" fill="none" stroke="var(--ink)" stroke-width="2"/>
        <rect x="834" y="474" width="14" height="10" rx="1" fill="var(--ink)"/>
        <path d="M834,475 L841,480 L848,475" fill="none" stroke="var(--card)" stroke-width="1.2"/>
      </g>
    </svg>
  </div>

</main>
</body>
</html>
```